Fernwick Landscaping Folder Design

I need a graphic designer to design a folder so we can insert informational sheets inside it for customers. The folder must include the company logo, project images, on front and back of folder and slogan " The Experience You Want, The Service You Expect, And The Value You Deserve'

Folder to also include phone numbers : 416 555 0193 as well as the website: www.fernwicklandscaping.example as well as we gurantee a 24 month warranty.

I have attached sample of size we need.

Pixel Harbor has also done something similar for me for Tollbridge Landscapes

Target Market(s)

geared toward home owners & commercial/industrial

Industry/Entity Type

Landscaping

Font styles to use
Other font styles liked:
• open to new trendy font

Requirements
Must have
• Telephone Number, email address, slogan, images,
Nice to have
• images of completed projects incorporated into the front and back of folder as well as the logo
Should not have
• n/a

```html
<!DOCTYPE html>
<html lang="en">
<head>
<meta charset="utf-8">
<title>Fernwick Landscaping Folder</title>
<link href="https://fonts.googleapis.com/css2?family=Oswald:wght@400;700&family=Roboto:wght@400;700&display=swap" rel="stylesheet">
<style>
  :root {
    --page-bg: #e9e6e1;
    --folder-black: #0c0c0d;
    --folder-sheen: #2a2a2c;
    --slogan-soft: #2b2b2d;
    --slogan-strong: #3a3a3c;
    --hex-dark: #151516;
    --hex-line: #000000;
    --band-blue: #1c3a8f;
    --text-white: #f2f2f2;
    --text-green: #3fbf4f;
    --logo-grey: #8a8a8c;
  }
  * { margin: 0; padding: 0; box-sizing: border-box; }
  html, body { width: 1200px; height: 848px; overflow: hidden; }
  body {
    background: var(--page-bg);
    position: relative;
    font-family: "Roboto", Arial, sans-serif;
  }
  .folder-panel {
    position: absolute;
    top: 127px;
    width: 420px;
    height: 594px;
    background: linear-gradient(150deg, var(--folder-sheen) 0%, var(--folder-black) 45%, var(--folder-black) 100%);
    box-shadow: 0 10px 28px rgba(0,0,0,.35);
    overflow: hidden;
  }
  .folder-front { left: 150px; }
  .folder-back { left: 630px; }

  .slogan {
    position: absolute;
    left: 40px;
    top: 120px;
    font-family: "Oswald", "Arial Narrow", sans-serif;
    text-transform: uppercase;
    font-size: 46px;
    line-height: 1.02;
    letter-spacing: .5px;
  }
  .slogan .soft { display: block; font-weight: 400; color: var(--slogan-soft); }
  .slogan .strong { display: block; font-weight: 700; color: var(--slogan-strong); }

  .brand-name {
    position: absolute;
    right: 34px;
    bottom: 58px;
    display: flex;
    align-items: center;
    gap: 10px;
    font-family: "Oswald", "Arial Narrow", sans-serif;
    font-weight: 700;
    font-size: 20px;
    text-transform: uppercase;
    letter-spacing: 1px;
    color: var(--logo-grey);
  }
  .brand-mark { width: 12px; height: 12px; background: var(--logo-grey); }

  .hex-grid { position: absolute; left: 0; top: 0; width: 420px; height: 420px; }

  .warranty-band {
    position: absolute;
    left: 0; top: 402px;
    width: 100%;
    height: 20px;
    background: var(--band-blue);
    color: var(--text-white);
    font-size: 10px;
    font-weight: 700;
    letter-spacing: .6px;
    text-transform: uppercase;
    text-align: center;
    line-height: 20px;
  }
  .contact-list {
    position: absolute;
    left: 150px; top: 440px;
    list-style: none;
    font-size: 11px;
  }
  .contact-list li { display: flex; align-items: center; gap: 7px; margin-bottom: 8px; color: var(--text-green); }
  .contact-list svg { width: 10px; height: 10px; }
</style>
</head>
<body>

<section class="folder-panel folder-front" aria-label="Folder front cover">
  <h1 class="slogan">
    <span class="soft">The Experience</span>
    <span class="strong">You Want,</span>
    <span class="soft">The Service</span>
    <span class="strong">You Expect,</span>
    <span class="soft">And The Value</span>
    <span class="strong">You Deserve</span>
  </h1>
  <div class="brand-name"><span class="brand-mark"></span>Fernwick Landscaping</div>
</section>

<section class="folder-panel folder-back" aria-label="Folder back cover">
  <svg class="hex-grid" viewBox="0 0 420 420" aria-hidden="false">
    <defs>
      <polygon id="hex" points="-75,0 -40,-50 40,-50 75,0 40,50 -40,50"/>
      <linearGradient id="photo-paving" x1="0" y1="0" x2="1" y2="1">
        <stop offset="0" stop-color="#b9b7b2"/><stop offset="1" stop-color="#7d7a74"/>
      </linearGradient>
      <linearGradient id="photo-pool" x1="0" y1="0" x2="1" y2="1">
        <stop offset="0" stop-color="#5a6b4a"/><stop offset=".5" stop-color="#2f7fd0"/><stop offset="1" stop-color="#6b6660"/>
      </linearGradient>
      <linearGradient id="photo-winter" x1="0" y1="0" x2="1" y2="1">
        <stop offset="0" stop-color="#9a9a9a"/><stop offset="1" stop-color="#4a4a4a"/>
      </linearGradient>
      <linearGradient id="photo-driveway" x1="0" y1="0" x2="1" y2="1">
        <stop offset="0" stop-color="#d8d8d6"/><stop offset="1" stop-color="#8e8f8a"/>
      </linearGradient>
      <linearGradient id="photo-garden" x1="0" y1="0" x2="1" y2="1">
        <stop offset="0" stop-color="#4f6b3a"/><stop offset="1" stop-color="#8c8c88"/>
      </linearGradient>
      <linearGradient id="photo-patio" x1="0" y1="0" x2="1" y2="1">
        <stop offset="0" stop-color="#e2ddd2"/><stop offset="1" stop-color="#a39a88"/>
      </linearGradient>
    </defs>
    <g fill="var(--hex-dark)" stroke="var(--hex-line)" stroke-width="6">
      <use href="#hex" x="40" y="0"/><use href="#hex" x="40" y="100"/><use href="#hex" x="40" y="200"/><use href="#hex" x="40" y="300"/><use href="#hex" x="40" y="400"/>
      <use href="#hex" x="155" y="-50"/><use href="#hex" x="155" y="50"/><use href="#hex" x="155" y="150"/><use href="#hex" x="155" y="250"/><use href="#hex" x="155" y="350"/>
      <use href="#hex" x="270" y="0"/><use href="#hex" x="270" y="100"/><use href="#hex" x="270" y="200"/><use href="#hex" x="270" y="300"/><use href="#hex" x="270" y="400"/>
      <use href="#hex" x="385" y="-50"/><use href="#hex" x="385" y="50"/><use href="#hex" x="385" y="150"/><use href="#hex" x="385" y="250"/><use href="#hex" x="385" y="350"/>
    </g>
    <g stroke="var(--hex-line)" stroke-width="6">
      <g role="img" aria-label="Photo of a commercial paving site with crew at work"><use href="#hex" x="40" y="100" fill="url(#photo-paving)"/></g>
      <g role="img" aria-label="Photo of a backyard pool with stone surround"><use href="#hex" x="155" y="150" fill="url(#photo-pool)"/></g>
      <g role="img" aria-label="Photo of a snow-covered property in winter"><use href="#hex" x="385" y="50" fill="url(#photo-winter)"/></g>
      <g role="img" aria-label="Photo of a finished concrete driveway"><use href="#hex" x="270" y="200" fill="url(#photo-driveway)"/></g>
      <g role="img" aria-label="Photo of interlock stone steps with garden planting"><use href="#hex" x="155" y="250" fill="url(#photo-garden)"/></g>
      <g role="img" aria-label="Photo of an interlock patio in front of a garage"><use href="#hex" x="270" y="300" fill="url(#photo-patio)"/></g>
    </g>
  </svg>

  <p class="warranty-band">We gurantee a 24 month warranty</p>

  <ul class="contact-list">
    <li>
      <svg viewBox="0 0 10 10" aria-hidden="true"><circle cx="5" cy="5" r="5" fill="var(--text-white)"/><path d="M3.2 2.5l1 1-.5.7a3 3 0 0 0 2.1 2.1l.7-.5 1 1-.6.8C4.6 7.5 2.5 5.4 2.4 3.1z" fill="var(--folder-black)"/></svg>
      <span>416 555 0193</span>
    </li>
    <li>
      <svg viewBox="0 0 10 10" aria-hidden="true"><circle cx="5" cy="5" r="4.2" fill="none" stroke="var(--text-white)" stroke-width="1"/><path d="M1 5h8M5 1c-2 2.4-2 5.6 0 8M5 1c2 2.4 2 5.6 0 8" fill="none" stroke="var(--text-white)" stroke-width=".8"/></svg>
      <span>www.fernwicklandscaping.example</span>
    </li>
  </ul>
</section>

</body>
</html>
```